Valmora Company needs a Business Card Design

We just opened our business recently and we need a business card design. Our basic product are clothes and accessories. We would like to see designs that use bright colors like pink, light blue and purple. In addition to that kindly include also our address in the business card which our main office is located in Los Angeles, California.
The final design should communicate that we have affordable price yet high quality brand.

Target Market(s)

young and middle age women

Industry/Entity Type

Business

Contact Information for Business Card

Valmora Apparel and Accessories 4873 North Bellcrest St. Los Angeles California
Tel: 555-318-6492

Logo Text

Valmora's Apparel and Accessories

Font styles to use
Serif

Requirements
Must have
• there should be a graphic of a sexy lady wearing an elegant dress at the upper left corner of the business card.

```html
<!DOCTYPE html>
<html lang="en">
<head>
<meta charset="utf-8">
<title>Valmora Apparel and Accessories – Business Card</title>
<link href="https://fonts.googleapis.com/css2?family=Arimo:wght@400;700&display=swap" rel="stylesheet">
<style>
  :root {
    --page-bg: #e6e6e6;
    --card-bg: #f7d5d6;
    --brand-red: #e3222d;
    --ink: #222222;
    --figure-red: #e3262f;
    --figure-line: #2b2024;
  }
  html, body {
    margin: 0;
    padding: 0;
    width: 1200px;
    height: 902px;
    overflow: hidden;
    background: var(--page-bg);
  }
  .business-card {
    position: absolute;
    left: 80px;
    top: 154px;
    width: 1040px;
    height: 594px;
    background: var(--card-bg);
    font-family: "Arimo", Arial, sans-serif;
    color: var(--ink);
    box-shadow: 0 6px 24px rgba(0,0,0,0.12);
  }
  .brand-name {
    position: absolute;
    left: 70px;
    top: 88px;
    margin: 0;
    font-size: 90px;
    line-height: 1;
    font-weight: 700;
    color: var(--brand-red);
    letter-spacing: 1px;
  }
  .brand-tagline {
    position: absolute;
    left: 72px;
    top: 194px;
    margin: 0;
    font-size: 60px;
    line-height: 74px;
    font-weight: 700;
    color: var(--brand-red);
  }
  .contact {
    position: absolute;
    left: 73px;
    top: 466px;
    font-size: 27px;
    line-height: 1;
  }
  .contact-phone {
    display: flex;
    align-items: center;
    gap: 12px;
    margin-bottom: 22px;
  }
  .phone-icon {
    width: 28px;
    height: 26px;
    display: block;
  }
  .contact-address {
    margin: 0;
    font-style: normal;
  }
  .figure-illustration {
    position: absolute;
    left: 755px;
    top: 55px;
    width: 210px;
    height: 493px;
  }
</style>
</head>
<body>
  <div class="business-card">
    <h1 class="brand-name">VALMORA</h1>
    <p class="brand-tagline">APPAREL<br>AND<br>ACCESSORIES</p>

    <div class="contact">
      <div class="contact-phone">
        <svg class="phone-icon" viewBox="0 0 28 26" aria-hidden="true">
          <rect width="28" height="26" fill="var(--brand-red)"/>
          <path d="M6 10 Q14 4 22 10 L20 13 L17 11 L17 9 Q14 8 11 9 L11 11 L8 13 Z" fill="#fff"/>
          <rect x="9" y="13" width="10" height="7" rx="1" fill="#fff"/>
        </svg>
        <span>555-318-6492</span>
      </div>
      <address class="contact-address">4873 North Bellcrest St. Los Angeles California</address>
    </div>

    <svg class="figure-illustration" viewBox="0 0 210 493" role="img"
         aria-label="Illustration of an elegant woman in a wide-brimmed hat and a long red mermaid gown">
      <defs>
        <linearGradient id="figureFill" x1="0" y1="0" x2="0" y2="1">
          <stop offset="0" stop-color="var(--card-bg)"/>
          <stop offset="0.3" stop-color="#ec8c90"/>
          <stop offset="1" stop-color="var(--figure-red)"/>
        </linearGradient>
      </defs>
      <rect x="0" y="0" width="210" height="493" rx="18" fill="url(#figureFill)"/>
    </svg>
  </div>
</body>
</html>
```